landscaping core flute signs

I need core flutes created with business name and a few extra dot points for putting on fences for job sites 120cm x 120cm approx.
I want our old ones information with the new L logo and colour palette

```html
<!DOCTYPE html>
<html lang="en">
<head>
<meta charset="utf-8">
<title>Grounded Form – Site Sign</title>
<link href="https://fonts.googleapis.com/css2?family=Montserrat:wght@500;600;700&family=Cinzel:wght@500&display=swap" rel="stylesheet">
<style>
  :root {
    --backdrop: #9a9a9a;
    --sign-white: #ffffff;
    --ink: #2b2b2b;
    --leaf-green: #5f8c57;
    --swoosh-black: #111111;
  }
  html, body {
    margin: 0;
    width: 1200px;
    height: 829px;
    overflow: hidden;
    background: var(--backdrop);
  }
  .sign {
    position: absolute;
    left: 281px;
    top: 96px;
    width: 637px;
    height: 637px;
    background: var(--sign-white);
    overflow: hidden;
    font-family: "Montserrat", sans-serif;
    color: var(--ink);
  }
  .brand-mark {
    position: absolute;
    left: 247px;
    top: 38px;
    width: 142px;
    height: 142px;
    border-radius: 50%;
    background: var(--leaf-green);
  }
  .brand-name {
    position: absolute;
    left: 0;
    width: 100%;
    top: 192px;
    text-align: center;
    font-weight: 600;
    font-size: 34px;
    letter-spacing: 1px;
    line-height: 1;
    text-transform: uppercase;
    color: var(--swoosh-black);
  }
  .brand-rule {
    position: absolute;
    top: 252px;
    left: 175px;
    width: 287px;
    height: 2px;
    background: var(--swoosh-black);
  }
  .tagline {
    position: absolute;
    left: 0;
    width: 100%;
    top: 262px;
    text-align: center;
    font-family: "Cinzel", serif;
    font-size: 12.5px;
    letter-spacing: 3.4px;
    color: var(--leaf-green);
  }
  .services {
    position: absolute;
    left: 157px;
    top: 308px;
    margin: 0;
    padding: 0;
    list-style: none;
  }
  .services li {
    display: flex;
    align-items: center;
    height: 34px;
    margin-bottom: 16px;
    font-size: 24px;
    font-weight: 500;
  }
  .services li::before {
    content: "";
    width: 20px;
    height: 20px;
    border-radius: 50%;
    background: var(--leaf-green);
    margin-right: 12px;
  }
  .phone {
    position: absolute;
    left: 0;
    width: 100%;
    top: 452px;
    text-align: center;
    font-size: 52px;
    font-weight: 700;
    letter-spacing: 0.5px;
    line-height: 1;
  }
  .email {
    position: absolute;
    left: 0;
    width: 100%;
    top: 525px;
    text-align: center;
    font-size: 26px;
    font-weight: 600;
    line-height: 1;
  }
  .footer-wave {
    position: absolute;
    left: 0;
    bottom: 0;
    width: 637px;
    height: 637px;
  }
  .licence {
    position: absolute;
    left: 62px;
    top: 592px;
    font-size: 18px;
    font-weight: 700;
    color: var(--sign-white);
  }
</style>
</head>
<body>
  <div class="sign">
    <div class="brand-mark"></div>
    <div class="brand-name">Grounded Form</div>
    <div class="brand-rule"></div>
    <div class="tagline">STRUCTURAL LANDSCAPING</div>

    <ul class="services">
      <li>Paving &amp; Concreting</li>
      <li>Fencing &amp; Retaining</li>
      <li>Desgin &amp; Construct</li>
    </ul>

    <div class="phone">0400 123 456</div>
    <div class="email">sam@groundedform.com</div>

    <svg class="footer-wave" viewBox="0 0 796 796" aria-hidden="true">
      <path d="M300,712 C480,760 650,770 796,712 L796,752 C650,790 480,780 300,712 Z" fill="var(--swoosh-black)"/>
      <path d="M0,742 C130,680 300,688 450,722" fill="none" stroke="var(--leaf-green)" stroke-width="4"/>
      <path d="M0,768 C120,700 300,698 420,734 C560,778 700,784 796,770 L796,796 L0,796 Z" fill="var(--leaf-green)"/>
    </svg>

    <div class="licence">QBSA:&nbsp; 1234567</div>
  </div>
</body>
</html>
```